I would like a business card to match my truck wrap and logo. I would like the font to match my existing business card please.

Industry/Entity Type

Painter

Contact Information for Business Card

Rodrigo Fenwar 801-437-2190 Fenwarcoatings.utah@brelmox.com
SERVICES - Custom Paint & Stain, Interior & Exterior, Epoxy Coatings / Garage Floors, Cabinet Refinishing, Log Staining and Refinishing.

Requirements
Nice to have
• I would like to have the white and grey line like the bottom of my vehicle wrap, Light Grey to match my truck also.

```html
<!DOCTYPE html>
<html lang="en">
<head>
<meta charset="utf-8">
<title>Fenwar Coatings – Business Card</title>
<link rel="stylesheet" href="https://fonts.googleapis.com/css2?family=Arimo:wght@400;700&display=swap">
<style>
  :root {
    --bg: #1e1e20;
    --card-white: #ffffff;
    --band-grey: #abafba;
    --brand-blue: #139fe0;
    --text-white: #ffffff;
  }
  * { margin: 0; padding: 0; box-sizing: border-box; }
  html, body { width: 1200px; height: 1015px; overflow: hidden; background: var(--bg); }
  body { font-family: "Arimo", Arial, sans-serif; position: relative; }

  .card {
    position: absolute;
    left: 190px;
    width: 820px;
    height: 440px;
    background: var(--card-white);
    overflow: hidden;
  }
  .card--back { top: 50px; }
  .card--front { top: 525px; }
  .card svg.bands { position: absolute; inset: 0; }
  .band { fill: var(--band-grey); }
  .band-line { fill: none; stroke: var(--band-grey); stroke-width: 9; }

  .services {
    position: absolute;
    left: 48px;
    top: 36px;
    color: var(--text-white);
    font-size: 22px;
    line-height: 1.3;
  }
  .services__title { font-weight: 700; font-size: 24px; margin-bottom: 4px; }
  .services__list { list-style: none; }
  .services__list li { white-space: nowrap; }
  .services__list li::before {
    content: "";
    display: inline-block;
    width: 10px; height: 10px;
    background: var(--text-white);
    transform: rotate(45deg);
    margin: 0 14px 2px 6px;
  }

  .brand {
    position: absolute;
    display: flex;
    align-items: center;
    gap: 16px;
    color: var(--brand-blue);
    font-weight: 700;
    font-size: 40px;
    text-transform: uppercase;
    letter-spacing: 2px;
    white-space: nowrap;
  }
  .card--back .brand { right: 60px; top: 310px; }
  .card--front .brand { left: 70px; top: 130px; }
  .brand__square { width: 56px; height: 56px; background: var(--brand-blue); border-radius: 6px; flex: none; }

  .contact {
    position: absolute;
    right: 44px;
    bottom: 70px;
    text-align: right;
    color: var(--text-white);
  }
  .contact__name { font-weight: 700; font-size: 30px; text-transform: uppercase; margin-bottom: 16px; }
  .contact__row { font-size: 20px; display: flex; justify-content: flex-end; align-items: center; gap: 10px; margin-top: 6px; }
  .contact__row svg { width: 20px; height: 20px; fill: var(--text-white); }
</style>
</head>
<body>

<section class="card card--back">
  <svg class="bands" viewBox="0 0 820 440" aria-hidden="true">
    <polygon class="band" points="0,0 820,0 820,60 560,60 520,250 0,250"/>
    <polyline class="band-line" points="820,80 576,80 536,270 0,270"/>
  </svg>
  <div class="services">
    <p class="services__title">SERVICES</p>
    <ul class="services__list">
      <li>Custom Paint &amp; Stain</li>
      <li>Interior &amp; Exterior</li>
      <li>Epoxy Coatings / Garage Floors</li>
      <li>Cabinet Refinishing</li>
      <li>Log Staining and Refinishing.</li>
    </ul>
  </div>
  <div class="brand"><span class="brand__square"></span><span>Fenwar Coatings</span></div>
</section>

<section class="card card--front">
  <svg class="bands" viewBox="0 0 820 440" aria-hidden="true">
    <polygon class="band" points="820,440 0,440 0,404 370,404 410,200 820,200"/>
    <polyline class="band-line" points="0,384 355,384 395,180 820,180"/>
  </svg>
  <div class="brand"><span class="brand__square"></span><span>Fenwar Coatings</span></div>
  <div class="contact">
    <p class="contact__name">Rodrigo Fenwar</p>
    <p class="contact__row">801-437-2190
      <svg viewBox="0 0 24 24"><path d="M6.6 10.8a15 15 0 0 0 6.6 6.6l2.2-2.2a1 1 0 0 1 1-.25 11.4 11.4 0 0 0 3.6.57 1 1 0 0 1 1 1V20a1 1 0 0 1-1 1A17 17 0 0 1 3 4a1 1 0 0 1 1-1h3.5a1 1 0 0 1 1 1c0 1.25.2 2.45.57 3.6a1 1 0 0 1-.25 1z"/></svg>
    </p>
    <p class="contact__row">Fenwarcoatings.utah@brelmox.com
      <svg viewBox="0 0 24 24"><path d="M2 5h20v14H2z M3.5 6.5 12 13l8.5-6.5" stroke="#abafba" stroke-width="1.5"/></svg>
    </p>
  </div>
</section>

</body>
</html>
```